Talvique Hotels Business Card and Logo

We need a business card design for a hotel group. I saw a hotel card you designed and really liked it. We have multiple properties with different brands. Were hoping that the card would be unique and find a way to list out all our properties. Our web address is www.talviquehotels.com. I have attached some photos of card designs I like.

Industry/Entity Type

Hotel

Contact Information for Business Card

Scott CurranReneson HotelsChief Operating Officer56 Madera DriveCorte Madera, CA 94925Office 415-891-5013Cell 707-5550143

```html
<!DOCTYPE html>
<html lang="en">
<head>
<meta charset="utf-8">
<title>Talvique Hotels — Business Card</title>
<link rel="stylesheet" href="https://fonts.googleapis.com/css2?family=Cinzel:wght@500&family=EB+Garamond:wght@400;500;600&display=swap">
<style>
  :root {
    --backdrop: #f1f1f1;
    --gold-top: #9f7520;
    --gold-bottom: #e4ae45;
    --ink: #111111;
    --card-white: #fdfdfd;
    --text-body: #3a3a3a;
    --text-muted: #555555;
  }
  * { margin: 0; padding: 0; box-sizing: border-box; }
  html, body {
    width: 1200px;
    height: 757px;
    overflow: hidden;
    background: var(--backdrop);
  }
  .canvas {
    position: relative;
    width: 1200px;
    height: 757px;
    background: var(--backdrop);
  }
  .card {
    position: absolute;
  }
  .card-front {
    left: 190px;
    top: 95px;
    width: 299px;
    height: 498px;
    background: linear-gradient(180deg, var(--gold-top) 0%, var(--gold-bottom) 100%);
  }
  .brand-name {
    position: absolute;
    left: 0;
    right: 0;
    top: 222px;
    text-align: center;
    font-family: "Cinzel", serif;
    font-weight: 500;
    font-size: 23px;
    line-height: 1.2;
    letter-spacing: 2px;
    color: var(--ink);
  }
  .brand-name .line {
    display: block;
  }
  .website {
    position: absolute;
    left: 0;
    right: 0;
    top: 537px;
    top: 442px;
    text-align: center;
    font-family: "EB Garamond", serif;
    font-size: 11.5px;
    letter-spacing: 3px;
    color: var(--ink);
  }
  .card-back {
    left: 582px;
    top: 225px;
    width: 500px;
    height: 300px;
    background: var(--card-white);
  }
  .person {
    position: absolute;
    left: 0;
    right: 0;
    top: 73px;
    text-align: center;
    font-family: "EB Garamond", serif;
  }
  .person-name {
    font-size: 16.5px;
    font-weight: 600;
    letter-spacing: 0.6px;
    color: var(--ink);
    line-height: 1.2;
  }
  .person-title {
    font-size: 10.5px;
    color: var(--text-muted);
    line-height: 1.3;
  }
  .contact {
    position: absolute;
    left: 0;
    right: 0;
    top: 222px;
    text-align: center;
    font-family: "EB Garamond", serif;
    font-size: 12px;
    line-height: 19px;
    color: var(--text-body);
  }
</style>
</head>
<body>
  <main class="canvas">
    <section class="card card-front" aria-label="Card front">
      <div class="brand-name">
        <span class="line">TALVIQUE</span>
        <span class="line">HOTELS</span>
      </div>
      <p class="website">www.talviquehotels.com</p>
    </section>

    <section class="card card-back" aria-label="Card back">
      <div class="person">
        <p class="person-name">BRENT HOLLOWAY</p>
        <p class="person-title">Chief Operating Officer</p>
      </div>
      <div class="contact">
        <p class="contact-phone">T: 415-555-0186 | M: 707-5550143</p>
        <p class="contact-address">83 Pellwick Lane Larkmoor, CA 94938</p>
      </div>
    </section>
  </main>
</body>
</html>
```